Job Recruiting Agemcy

almost like my current site www.plorvex.com but with these changes see and what i meant about the across the to the site says home job companies categories pages blog and login sign up that should only be the 4 i said only 1 home 2 industries 3 jobs 4 contact us. and remove latest blog post and our partners because that's not us we have to post acuarte information thanks and the name of the company if your using is is work and careful hiring partners and want it easy for us to post and remove jobs and where it emails us every resume or person that applies

Requirements
Must have
• must send email to us when an application is submitted and try to incorparate the colors of current site
Nice to have
• i want a pretty basic site for now just like the one i have but with all thats above were its easy for me being the own to be able to post jobs and everything

```html
<!DOCTYPE html>
<html lang="en">
<head>
<meta charset="utf-8">
<title>Plorvex – Work and Careful Hiring Partners</title>
<link href="https://fonts.googleapis.com/css2?family=Roboto:wght@400;500;700;900&display=swap" rel="stylesheet">
<style>
:root{
  --green:#3f6e4c;
  --green-dark:#2f5a3b;
  --pink:#e2325f;
  --purple:#7b1fd6;
  --ink:#1b1b1b;
  --muted:#666;
  --teal:#2a9d8f;
  --job-title:#2f6b3e;
  --grey-bg:#f1f1f1;
  --footer:#232323;
  --footer-bottom:#1a1a1a;
  --grad:linear-gradient(90deg,var(--pink),var(--purple));
}
*{box-sizing:border-box;margin:0;padding:0}
html,body{width:1200px;height:4049px;overflow:hidden}
body{position:relative;font-family:'Roboto',sans-serif;color:var(--ink);background:#fff}
.abs{position:absolute}
.center{text-align:center;left:0;width:1200px}

/* header */
.site-header{position:absolute;top:0;left:0;width:1200px;height:97px;background:var(--green);z-index:3}
.brand{position:absolute;left:106px;top:-30px;width:192px;height:195px;border-radius:50%;background:var(--green);display:flex;flex-direction:column;align-items:center;justify-content:flex-end;padding-bottom:34px}
.brand-name{font-weight:900;font-size:22px;color:#e2325f;letter-spacing:1px}
.brand-tag{font-size:6px;color:#111;font-weight:700;margin-top:3px;letter-spacing:.3px;text-transform:uppercase}
.main-nav{position:absolute;top:38px;left:520px;display:flex;gap:0}
.main-nav a{position:absolute;font-size:14px;font-weight:700;color:#fff;text-decoration:none;white-space:nowrap}
.main-nav a.active{color:#ff6b7a}
.main-nav a.active::after{content:"";position:absolute;left:-2px;right:-2px;top:26px;height:3px;background:var(--pink)}
.search-ico{position:absolute;left:922px;top:40px}
.login-btn{position:absolute;left:980px;top:28px;width:108px;height:38px;border-radius:19px;background:var(--grad);color:#fff;font-size:14px;font-weight:500;display:flex;align-items:center;justify-content:center;gap:6px}

/* hero */
.hero{position:absolute;top:97px;left:0;width:1200px;height:601px;background:linear-gradient(180deg,#43506a 0%,#c46a50 28%,#e2884e 36%,#3a3c4c 55%,#2b2f3c 75%,#4a3b3e 100%)}
.hero-kicker{top:318px;font-size:20px;font-weight:500;color:#fff}
.hero-title{top:348px;font-size:40px;font-weight:700;color:#fff}
.hero-line{position:absolute;top:440px;left:0;width:1200px;height:22px;background:rgba(0,0,0,.75)}
.search-bar{position:absolute;top:432px;left:197px;width:802px;height:40px;background:#fff;border-radius:20px;display:flex;align-items:center;font-size:12px;color:#777}
.search-bar .kw{width:447px;padding-left:20px;display:flex;gap:8px;align-items:center;border-right:1px solid #ddd;height:100%}
.search-bar .loc{flex:1;padding-left:16px;display:flex;gap:8px;align-items:center}
.search-bar .go{width:118px;height:40px;border-radius:20px;background:var(--grad);color:#fff;font-weight:700;font-size:15px;display:flex;align-items:center;justify-content:center}
.slide-arrow{position:absolute;top:380px;width:36px;height:36px;border:2px solid #fff;border-radius:50%;display:flex;align-items:center;justify-content:center}

/* welcome */
.welcome{position:absolute;top:698px;left:0;width:1200px;height:186px;background:linear-gradient(90deg,#e04563 0%,#c03a8a 50%,#7c1fd4 100%);color:#fff;text-align:center}
.welcome h2{font-size:30px;font-weight:700;margin-top:36px}
.welcome p{font-size:16px;font-weight:500;line-height:28px;width:900px;margin:18px auto 0}

/* section titles */
.section-title{position:absolute;left:0;width:1200px;text-align:center;font-size:34px;font-weight:700;color:var(--ink)}
.section-title::after{content:"";display:block;width:98px;height:4px;margin:12px auto 0;background:var(--grad);border-radius:2px}

/* industries */
.industry-card{position:absolute;top:1082px;width:231px;height:208px;background:#fff;box-shadow:0 2px 10px rgba(0,0,0,.14);text-align:center}
.industry-card svg{margin-top:48px}
.industry-card h3{font-size:16px;font-weight:700;margin-top:14px}
.industry-card p{font-size:13px;color:var(--muted);margin-top:8px}
.industry-card.featured{background:linear-gradient(135deg,#d23a63,#7a1fd4);color:#fff}
.industry-card.featured p{color:#f3dff0}
.outline-btn{position:absolute;border:2px solid var(--pink);border-radius:26px;color:#8a2ab8;font-weight:700;display:flex;align-items:center;justify-content:center;gap:8px;background:#fff}

/* jobs */
.jobs-band{position:absolute;top:1507px;left:0;width:1200px;height:1029px;background:var(--grey-bg)}
.job-card{position:absolute;left:126px;width:948px;height:162px;background:#fff;box-shadow:0 1px 4px rgba(0,0,0,.06)}
.job-logo{position:absolute;left:14px;top:0;width:156px;height:162px;display:flex;align-items:center;justify-content:center;font-size:19px;font-weight:700;color:#1d4a8a}
.job-type{position:absolute;left:207px;top:27px;font-size:13px;color:var(--teal)}
.job-title{position:absolute;left:207px;top:47px;font-size:18px;font-weight:500;color:var(--job-title);display:flex;gap:10px;align-items:center}
.job-posted{position:absolute;left:207px;top:74px;font-size:13px;color:#333}
.job-meta{position:absolute;left:207px;top:106px;font-size:13px;color:#444;display:flex;gap:24px}
.job-meta span{display:flex;gap:6px;align-items:center}
.browse-job{position:absolute;right:25px;top:59px;width:160px;height:44px;border:2px solid var(--pink);border-radius:22px;color:#8a2ab8;font-weight:700;font-size:14px;display:flex;align-items:center;justify-content:center}
.solid-btn{position:absolute;border-radius:26px;background:var(--grad);color:#fff;font-weight:700;display:flex;align-items:center;justify-content:center}

/* testimonials */
.testimonial{position:absolute;top:2742px;width:310px;height:192px}
.testimonial .bubble{position:absolute;inset:0;border:1px solid #ddd;border-top:none;border-radius:12px;background:#fff}
.testimonial .top-line{position:absolute;top:0;height:3px;background:var(--grad)}
.testimonial .avatar{position:absolute;left:111px;top:-44px;width:88px;height:88px;border-radius:50%;background:radial-gradient(circle at 50% 40%,#e7c9ae,#8a6a58);border:3px solid #fff}
.testimonial p{position:absolute;top:74px;left:28px;right:28px;font-size:14px;line-height:26px;text-align:center;color:#444}
.testimonial .pointer{position:absolute;left:147px;bottom:-9px;width:16px;height:16px;background:#fff;border-right:1px solid #ddd;border-bottom:1px solid #ddd;transform:rotate(45deg)}
.client{position:absolute;top:2957px;width:310px;text-align:center;font-size:15px;font-weight:700;color:#222}
.client small{font-size:10px;font-weight:400}
.stars{position:absolute;top:2980px;width:310px;text-align:center;color:#f5c400;font-size:13px;letter-spacing:1px}

/* contact */
.contact{position:absolute;top:3094px;left:0;width:1200px;height:604px;background:linear-gradient(180deg,#3f6e4c 0%,#4e7a58 55%,#6e9177 100%)}
.contact .section-title{color:#fff}
.contact .section-title::after{background:#fff}
.field{position:absolute;background:#fff;font-size:14px;color:#555;padding:20px 22px}

/* footer */
.footer{position:absolute;top:3698px;left:0;width:1200px;height:292px;background:var(--footer);color:#fff}
.footer h4{position:absolute;top:76px;font-size:18px;font-weight:700}
.footer .line{position:absolute;font-size:14px;display:flex;gap:12px;align-items:flex-start;line-height:22px}
.footer .link{position:absolute;font-size:14px}
.sub-input{position:absolute;left:716px;top:121px;width:234px;height:46px;border-radius:23px;background:#fff;color:#555;font-size:12px;padding:15px 22px}
.social{position:absolute;top:234px;width:30px;height:30px;border:1.5px solid #fff;border-radius:50%}
.copyright{position:absolute;top:3990px;left:0;width:1200px;height:59px;background:var(--footer-bottom);color:#fff;font-size:13px;text-align:center;line-height:59px}
</style>
</head>
<body>

<header class="site-header">
  <div class="brand">
    <div class="brand-name">PLORVEX</div>
    <div class="brand-tag">work and careful hiring partners</div>
  </div>
  <nav class="main-nav">
    <a class="active" style="left:0">HOME</a>
    <a style="left:80px">INDUSTRIES</a>
    <a style="left:201px">JOBS</a>
    <a style="left:275px">CONTACT US</a>
  </nav>
  <svg class="search-ico" width="16" height="16" viewBox="0 0 16 16"><circle cx="6.5" cy="6.5" r="5" fill="none" stroke="#fff" stroke-width="2"/><line x1="10" y1="10" x2="15" y2="15" stroke="#fff" stroke-width="2"/></svg>
  <div class="login-btn"><svg width="10" height="12" viewBox="0 0 10 12"><rect x="0" y="5" width="10" height="7" rx="1" fill="#fff"/><path d="M2 5V3.5a3 3 0 0 1 6 0V5" fill="none" stroke="#fff" stroke-width="1.5"/></svg>Login</div>
</header>

<section class="hero" role="img" aria-label="Silhouettes of business people shaking hands against a city skyline at sunset">
</section>
<div class="abs center hero-kicker">SEARCH FROM 0 JOB OFFERS</div>
<h1 class="abs center hero-title">YOUR CAREER STARTS HERE!</h1>
<div class="hero-line"></div>
<div class="search-bar">
  <div class="kw"><svg width="12" height="12" viewBox="0 0 16 16"><circle cx="6.5" cy="6.5" r="5" fill="none" stroke="#555" stroke-width="2.2"/><line x1="10" y1="10" x2="15" y2="15" stroke="#555" stroke-width="2.2"/></svg>Job Title, Skills And Keywords</div>
  <div class="loc"><svg width="9" height="12" viewBox="0 0 10 14"><path d="M5 0a5 5 0 0 1 5 5c0 4-5 9-5 9S0 9 0 5a5 5 0 0 1 5-5z" fill="#555"/><circle cx="5" cy="5" r="2" fill="#fff"/></svg>City, Zip Codes</div>
  <div class="go">SEARCH</div>
</div>
<div class="slide-arrow" style="left:34px"><svg width="10" height="14" viewBox="0 0 10 14"><path d="M8 1 2 7l6 6" fill="none" stroke="#fff" stroke-width="2"/></svg></div>
<div class="slide-arrow" style="left:1126px"><svg width="10" height="14" viewBox="0 0 10 14"><path d="M2 1l6 6-6 6" fill="none" stroke="#fff" stroke-width="2"/></svg></div>

<section class="welcome">
  <h2>WELCOME TO PLORVEX</h2>
  <p>We have over 35 years of Specialized Recruiting and souring experience. We cover a broad spectrum of industries to include some of the top aerospace and pharmaceutical commercial companies of today.</p>
</section>

<h2 class="section-title" style="top:978px">INDUSTRIES WE SUPPORT</h2>

<div class="industry-card" style="left:110px">
  <svg width="54" height="54" viewBox="0 0 54 54" fill="none" stroke="#d43a6a" stroke-width="2"><path d="M34 4c8 4 10 14 6 24l-6 4-6-4c-4-10-2-20 6-24z"/><circle cx="34" cy="16" r="3"/><path d="M28 28l-5 6M40 28l5 6"/><circle cx="16" cy="24" r="6"/><path d="M4 50v-8a12 12 0 0 1 24 0v8z"/></svg>
  <h3>Aero Space</h3><p>5 Open Positions</p>
</div>
<div class="industry-card" style="left:360px">
  <svg width="54" height="54" viewBox="0 0 54 54" fill="none" stroke="#d43a6a" stroke-width="2"><path d="M18 14h10v6l6 8v20H12V28l6-8z"/><rect x="32" y="32" width="16" height="16" rx="2"/><circle cx="40" cy="40" r="3"/><circle cx="22" cy="6" r="2"/><circle cx="30" cy="4" r="1.5"/></svg>
  <h3>Pharmaceutical</h3><p>5 Open Positions</p>
</div>
<div class="industry-card featured" style="left:609px">
  <svg width="54" height="54" viewBox="0 0 54 54" fill="none" stroke="#fff" stroke-width="2"><path d="M6 14l16 4 14-8c4-2 8 0 6 3l-12 9 4 14-4 2-8-12-10 4-2 4-3-1 1-7z"/><rect x="10" y="36" width="22" height="12"/><path d="M32 40h8l4 5v3H32"/><circle cx="16" cy="50" r="2"/><circle cx="38" cy="50" r="2"/></svg>
  <h3>Transportation</h3><p>5 Open Positions</p>
</div>
<div class="industry-card" style="left:857px">
  <svg width="54" height="54" viewBox="0 0 54 54" fill="none" stroke="#d43a6a" stroke-width="2"><rect x="16" y="8" width="26" height="36" rx="2"/><path d="M10 24c0-6 8-8 10-2 2-6 10-4 10 2 0 6-10 12-10 12S10 30 10 24z"/><path d="M44 6l6 3v6c0 4-6 7-6 7s-6-3-6-7V9z"/><path d="M42 14h4M44 12v4"/></svg>
  <h3>Medical</h3><p>5 Open Positions</p>
</div>

<div class="outline-btn" style="left:456px;top:1335px;width:288px;height:51px;font-size:16px">BROWSE ALL CATEGORIES
  <svg width="16" height="16" viewBox="0 0 16 16"><circle cx="8" cy="8" r="8" fill="#8a2ab8"/><path d="M6 4l4 4-4 4" fill="none" stroke="#fff" stroke-width="2"/></svg></div>

<section class="jobs-band"></section>
<h2 class="section-title" style="top:1556px">FEATURED JOBS</h2>

<article class="job-card" style="top:1655px">
  <div class="job-logo">Brightwire</div>
  <div class="job-type">Freelance</div>
  <div class="job-title">Specification Engineer <span style="color:#f5b400">★</span></div>
  <div class="job-posted">Posted 3 years ago</div>
  <div class="job-meta"><span>📍 Seattle, WA, United States</span><span>💼 Brightwire Manufacturing</span><span>💵 $45 - $60/hour</span></div>
  <div class="browse-job">BROWSE JOB</div>
</article>
<article class="job-card" style="top:1847px">
  <div class="job-logo">Halvern Imaging</div>
  <div class="job-type">Full Time</div>
  <div class="job-title">Senior Account Executive <span style="color:#f5b400">★</span></div>
  <div class="job-posted">Posted 4 years ago</div>
  <div class="job-meta"><span>📍 New Jersey, United States</span><span>💼 Halvern Imaging</span><span>💵 $35 - $50/hour</span></div>
  <div class="browse-job">BROWSE JOB</div>
</article>
<article class="job-card" style="top:2039px">
  <div class="job-logo">Corwell</div>
  <div class="job-type">Full Time</div>
  <div class="job-title">Electrician (Manufacturing) <span style="color:#f5b400">★</span></div>
  <div class="job-posted">Posted 4 years ago</div>
  <div class="job-meta"><span>📍 Milpitas, CA, United States</span><span>💼 Corwell Engineering</span><span>💵 $14 - $18/hour</span></div>
  <div class="browse-job">BROWSE JOB</div>
</article>
<article class="job-card" style="top:2229px">
  <div class="job-logo">Maplecrest</div>
  <div class="job-type">Full Time</div>
  <div class="job-title">Admissions Coordinator <span style="color:#f5b400">★</span></div>
  <div class="job-posted">Posted 4 years ago</div>
  <div class="job-meta"><span>📍 Andover, MA, United States</span><span>💼 Maplecrest Healthcare</span><span>💵 $8 - $10/hour</span></div>
  <div class="browse-job">BROWSE JOB</div>
</article>

<div class="solid-btn" style="left:497px;top:2437px;width:206px;height:50px;font-size:16px">BROWSE ALL JOBS</div>

<h2 class="section-title" style="top:2626px">WHAT OUR CLIENTS SAY?</h2>

<div class="testimonial" style="left:110px">
  <div class="bubble"></div><div class="pointer"></div>
  <div class="top-line" style="left:0;width:310px"></div>
  <div class="avatar" role="img" aria-label="Client portrait"></div>
  <p>I didn't even need training. I couldn't have asked for more than this. It really saves me time and effort. Careerly is exactly what our business has been</p>
</div>
<div class="client" style="left:110px">Dana Merrow, <small>HR Manager in Orchard Inc.</small></div>
<div class="stars" style="left:110px">★★★★★</div>

<div class="testimonial" style="left:445px">
  <div class="bubble"></div><div class="pointer"></div>
  <div class="top-line" style="left:0;width:310px"></div>
  <div class="avatar" role="img" aria-label="Client portrait"></div>
  <p>I just can't get enough of Careerly. I want to get a T-Shirt with Careerly on it so I can show it off to everyone. This is simply unbelievable!</p>
</div>
<div class="client" style="left:445px">Evan Tosh, <small>Key Account Manager in Chirply Inc.</small></div>
<div class="stars" style="left:445px">★★★★★</div>

<div class="testimonial" style="left:779px">
  <div class="bubble"></div><div class="pointer"></div>
  <div class="top-line" style="left:0;width:310px"></div>
  <div class="avatar" role="img" aria-label="Client portrait"></div>
  <p>Thanks for the great service. Careerly has completely surpassed our expectations. Careerly is the most valuable business resource we have</p>
</div>
<div class="client" style="left:779px">Aaron Welby, <small>Brand Manager in Bidmart Inc.</small></div>
<div class="stars" style="left:779px">★★★★★</div>

<section class="contact" role="img" aria-label="Green tinted city skyline background">
  <h2 class="section-title" style="top:62px">CONTACT US</h2>
  <div class="field" style="left:176px;top:170px;width:414px;height:55px">First Name</div>
  <div class="field" style="left:610px;top:170px;width:414px;height:55px">Last Name</div>
  <div class="field" style="left:176px;top:242px;width:414px;height:54px">Email</div>
  <div class="field" style="left:610px;top:242px;width:414px;height:54px">Phone</div>
  <div class="field" style="left:176px;top:315px;width:848px;height:127px">Message</div>
  <div class="solid-btn" style="left:514px;top:488px;width:172px;height:50px;font-size:17px">SUBMIT</div>
</section>

<footer class="footer">
  <h4 style="left:110px">Contact Us</h4>
  <div class="line" style="left:110px;top:112px"><span style="color:#3f8f5a">●</span><span>18 Linden Street, Apt. 303<br>Harbor City, NY 10016 USA</span></div>
  <div class="line" style="left:110px;top:172px"><span style="color:#3f8f5a">✉</span><span>hello@plorvex.com</span></div>
  <div class="line" style="left:110px;top:208px"><span style="color:#3f8f5a">✆</span><span>+1 800 555 0142</span></div>
  <div class="line" style="left:110px;top:243px"><span style="color:#3f8f5a">▣</span><span>+1 555 014 7890</span></div>

  <h4 style="left:407px">Links</h4>
  <div class="link" style="left:409px;top:122px">Home</div>
  <div class="link" style="left:409px;top:149px">Industries</div>
  <div class="link" style="left:409px;top:175px">Jobs</div>
  <div class="link" style="left:409px;top:202px">Contact us</div>
  <div class="link" style="left:530px;top:122px">Terms &amp; Condition</div>
  <div class="link" style="left:530px;top:149px">Privacy Policy</div>
  <div class="link" style="left:530px;top:175px">Imprint</div>

  <h4 style="left:711px">Subscribe for Updates</h4>
  <div class="sub-input">Emaill Address</div>
  <div class="solid-btn" style="left:964px;top:121px;width:123px;height:46px;font-size:16px">SUBMIT</div>
  <div class="link" style="left:711px;top:180px;font-weight:500">☑&nbsp; Yes, Please Contact me.</div>
  <div class="social" style="left:711px"></div>
  <div class="social" style="left:753px"></div>
  <div class="social" style="left:795px"></div>
</footer>
<div class="copyright">© 2020 &nbsp;plorvex &nbsp;| &nbsp;All Rights Reserved</div>

</body>
</html>
```